TRELOS - Web Design Project

Task Description
RELOS is the major GLOVRA project supporting the Indonesian Bureau of Tidal Works and Harvests (BTWH). BTWH is responsible for promoting sustainable use of fish and other marine resources for Indonesia’s long-term economic prosperity. Its mandate encompasses such issues as drafting of marine and fisheries sector policies; control of overfishing, destructive and illegal fishing practices; spatial planning for resource use; management of conservation areas; data analysis and modeling for fisheries management; and promoting the long-term welfare of fishing communities. The TRELOS project is supporting BTWH efforts to achieve sustainability in the marine and fisheries sector and to improve the response of coastal communities to near-term disasters and long-term impacts related to climate change.

The TRELOS project has three key thematic areas: [policy] [1], [sustainable fisheries] [2], and [climate change] [3] — as well as supporting overall coordination of [Coastal Stewardship Scheme] [4] activities.
Updates

Project Deadline Extended
Reason: There are two public holidays in Indonesia so we are unable to provide feedback to designers between 17th and the 20th.

a few people have asked for reference sites - there is really no reference site we can give but I have attached a jpg for some ideas - we are after innovated ideas that will capture people's attention but which is extermely easy to use and navigate. 

the main focus should be on a map on Indonesia with focal points of our three offices (and with great navigation buttons/tools). 

please give us something amazing and use your design skills to make an amazing site

thanks

Target Market(s)

under 25, college or uni - research students - others interested in marine and fisheries

Industry/Entity Type

Sustainability

Requirements
Must have
• The web must have Indonesia map on the center with button on Jakarta city as headquarter, Sulawesi Tenggara (Wakatobi) as branch office and Nusa Tenggara Barat (Mataram), must have an icon for navigation on the upper, left or bottom side. Example of layout is attached (only as example). The "buttons" should then be used as navigation tools

We are after innovative ideas that with easy navigation features.

Current website is www.trelosworks.com - this is seen as too hard to navigate

Navigation Icons will also need to be developed;
- About
- Activities
- News
Library
Press releases
Publications
- Partners
- Links

site will also need to adhere to these the GLOVRA branding guidelines
http://www.glovra.example/identity/GLOVRA_Visual_Rules_Guide.pdf

TRELOS Logo is attached

Nice to have
• - based on scaffold plinko, site will be hosted on stavelo9 platform. (http://plinko.codebarn.example/)

```html
<!DOCTYPE html>
<html lang="en">
<head>
<meta charset="utf-8">
<title>TRELOS – Coastal and Climate Partnership</title>
<link rel="stylesheet" href="https://fonts.googleapis.com/css2?family=Arimo:wght@400;700&family=PT+Sans:wght@400;700&display=swap">
<style>
:root{
  --red:#c8102e;
  --navy:#0b2a5c;
  --blue:#0a57b8;
  --blue-deep:#063a86;
  --link:#1a4f9c;
  --text:#6b6b6b;
  --muted:#8a8a8a;
  --line:#e2e2e2;
  --white:#ffffff;
  --accent:#cc0000;
}
*{box-sizing:border-box;margin:0;padding:0}
html,body{width:941px;height:1200px;overflow:hidden}
body{position:relative;font-family:"Arimo",Arial,sans-serif;font-size:11.5px;color:var(--text);
  background:linear-gradient(#0d4ea8 0,#0b3f8c 60%,#0a2f6b 100%)}
.abs{position:absolute}
.topbar{left:0;top:0;width:941px;height:6px;background:var(--red)}
.header{left:0;top:6px;width:941px;height:120px;background:var(--white)}
.brand{left:23px;top:40px;width:290px}
.brand-name{display:flex;align-items:center;gap:9px;font-family:"PT Sans",sans-serif;font-weight:700;font-size:24px;color:var(--blue-deep)}
.brand-name .mark{width:22px;height:22px;background:var(--blue-deep)}
.brand-strap{margin-top:6px;font-size:9px;color:var(--muted);letter-spacing:.3px}
.phone{left:596px;top:93px;display:flex;align-items:center;gap:6px;font-size:13px;color:#9a9a9a}
.search{left:752px;top:93px;width:171px;height:25px;border:1px solid #cfcfcf;display:flex}
.search span{flex:1;font-size:11px;color:#bdbdbd;line-height:23px;padding-left:12px}
.search b{width:28px;background:var(--blue);display:flex;align-items:center;justify-content:center}
.nav{left:0;top:126px;width:941px;height:37px;background:linear-gradient(#fff,#eef0f3);border-top:1px solid #ddd;border-bottom:1px solid #ccc}
.nav a{position:absolute;top:0;height:36px;display:flex;align-items:center;gap:7px;font-family:"PT Sans",sans-serif;font-weight:400;font-size:12px;color:#b01030;text-decoration:none}
.nav a.active{background:var(--white);padding:0 10px 0 4px}
.nav i{display:block;width:20px;height:20px;border-radius:50%;background:var(--blue)}
.map{left:0;top:163px;width:941px;height:371px;background:radial-gradient(ellipse at 45% 40%,#dfe8f6 0,#6c97d6 28%,#0b57be 60%,#0846a0 100%)}
.pin{position:absolute;transform:translateX(-50%);text-align:center}
.pin .tag{background:var(--navy);color:var(--white);font-weight:700;font-size:10.5px;padding:4px 7px;position:relative}
.pin .tag:after{content:"";position:absolute;left:50%;bottom:-5px;margin-left:-5px;border:5px solid transparent;border-bottom:0;border-top-color:var(--navy)}
.pin .dot{width:11px;height:11px;border-radius:50%;background:#777;border:2px solid #ddd;margin:8px auto 0}
.panel{left:18px;top:534px;width:905px;height:574px;background:var(--white)}
.card{position:absolute;top:549px;width:205px;height:156px;background:linear-gradient(#fff,#f3f3f3);border:1px solid var(--line)}
.card h3{height:38px;display:flex;align-items:center;gap:8px;padding-left:8px;font-family:"PT Sans",sans-serif;font-size:13.5px;color:var(--blue-deep);line-height:15px;background:linear-gradient(#f5f5f5,#e9e9e9);border-bottom:1px solid var(--line)}
.card h3 i{width:30px;height:30px;border-radius:6px;flex:none}
.card p{padding:12px 9px 0 10px;line-height:18.5px;text-align:justify;font-size:11.3px}
.more{color:var(--accent);font-weight:700}
.sect{font-family:"PT Sans",sans-serif;font-weight:700;font-size:14px;color:var(--muted)}
.sect em{font-style:normal;color:var(--blue)}
.news-title{font-family:"PT Sans",sans-serif;font-weight:700;font-size:13px;color:var(--link);letter-spacing:.4px}
.news-text{line-height:18.5px;text-align:justify}
.news-text .more{font-weight:400}
.rule{height:1px;background:var(--line)}
.shot{position:absolute;top:10px;height:102px;background:linear-gradient(#6f9fd8 0,#e6eef7 45%,#5f8fb0 70%,#2c6f8a 100%)}
.play{position:absolute;left:50%;top:50%;margin:-13px 0 0 -12px;border:13px solid transparent;border-left:0;border-right:22px solid rgba(255,255,255,.8)}
.gallery{position:absolute;top:974px;height:123px;border:2px solid #dde3ee;background:var(--white)}
.arrow{position:absolute;width:24px;height:24px;border-radius:50%;background:var(--white);border:2px solid #d8dde6}
.box{position:absolute;left:701px;width:206px;border:1px solid var(--line);background:var(--white)}
.box h4{height:24px;line-height:24px;padding-left:12px;font-family:"PT Sans",sans-serif;font-size:14px;color:var(--navy);background:linear-gradient(#fff,#ececec)}
.box h4 em{font-style:normal;color:var(--accent)}
.event{margin:0 13px;padding:7px 0 8px;border-bottom:1px dashed #ddd;color:var(--link);font-size:11.3px;line-height:16px}
.event b{display:block;margin-bottom:2px}
.footer{left:18px;top:1122px;width:600px;color:#dfe7f4;font-size:10.3px;line-height:17.5px}
.footer-links{right:18px;top:1122px;color:var(--white);font-size:11.5px;word-spacing:2px}
.social{top:1152px;width:21px;height:21px;border-radius:3px}
</style>
</head>
<body>
<div class="abs topbar"></div>
<header class="abs header"></header>
<div class="abs brand">
  <div class="brand-name"><span class="mark"></span>GLOVRA Indonesia</div>
  <div class="brand-strap">Coastal and Climate Partnership (TRELOS) Project</div>
</div>
<div class="abs phone">
  <svg width="26" height="26" viewBox="0 0 26 26"><circle cx="16" cy="9" r="7" fill="none" stroke="#f0a020" stroke-width="2"/><path d="M5 4c-3 3-2 9 3 14s11 6 14 3l-4-4-3 2c-2-1-5-4-6-6l2-3z" fill="#222"/></svg>
  +62 21 555 0182
</div>
<div class="abs search"><span>Search something...</span><b><svg width="13" height="13" viewBox="0 0 13 13"><circle cx="5.5" cy="5.5" r="4" fill="none" stroke="#fff" stroke-width="2"/><path d="M8.5 8.5l3.5 3.5" stroke="#fff" stroke-width="2"/></svg></b></div>

<nav class="abs nav">
  <a class="active" style="left:16px"><i></i>ABOUT US</a>
  <a style="left:129px"><i></i>ACTIVITIES</a>
  <a style="left:243px"><i style="background:#b5894f"></i>NEWS</a>
  <a style="left:330px"><i style="border-radius:2px;background:#2d3f73"></i>LIBRARY</a>
  <a style="left:423px"><i style="border-radius:2px;background:#d23a3a"></i>PRESS RELEASE</a>
  <a style="left:550px"><i style="border-radius:3px;background:#3a86c8"></i>PUBLICITY</a>
  <a style="left:661px"><i style="background:#e2334a"></i>PARTNERS</a>
  <a style="left:778px"><i style="background:#8a9ac8"></i>LINKS</a>
</nav>

<section class="abs map" role="img" aria-label="Map of the Indonesian archipelago in white on deep blue, with office locations marked"></section>
<div class="pin" style="left:398px;top:362px"><div class="tag">SULAWESI</div><div class="dot"></div></div>
<div class="pin" style="left:222px;top:413px"><div class="tag">JAKARTA</div><div class="dot"></div></div>
<div class="pin" style="left:378px;top:436px"><div class="tag">LOMBOK</div><div class="dot"></div></div>

<main class="abs panel"></main>

<article class="card" style="left:35px"><h3><i role="img" aria-label="Policy folder icon" style="background:#1d5fae"></i>Policy</h3><p>Lorem ipsum dolor sit ipusmLorem ipsum dolor sit ipusmLorem ipsum dolor sit ipusmLorem ipsum dolor sit ipusmLorem ipsum dolor sit usm Lorem ipsum dolor. <span class="more">More...</span></p></article>
<article class="card" style="left:257px"><h3><i role="img" aria-label="Green fish icon" style="background:#8fc640"></i>Sustainable Fisheries</h3><p>Lorem ipsum dolor sit ipusmLorem ipsum dolor sit ipusmLorem ipsum dolor sit ipusmLorem ipsum dolor sit ipusmLorem ipsum dolor sit usm Lorem ipsum dolor. <span class="more">More...</span></p></article>
<article class="card" style="left:478px"><h3><i role="img" aria-label="Climate globe icon" style="border-radius:50%;background:linear-gradient(135deg,#2a7ad0,#6cbf3c)"></i>Climate Changes</h3><p>Lorem ipsum dolor sit ipusmLorem ipsum dolor sit ipusmLorem ipsum dolor sit ipusmLorem ipsum dolor sit ipusmLorem ipsum dolor sit usm Lorem ipsum dolor. <span class="more">More...</span></p></article>
<article class="card" style="left:701px"><h3><i role="img" aria-label="Sailboat icon" style="background:#1a63c0"></i>Marine Resources<br>Programme</h3><p>Lorem ipsum dolor sit ipusmLorem ipsum dolor sit ipusmLorem ipsum dolor sit ipusmLorem ipsum dolor sit ipusmLorem ipsum dolor sit usm Lorem ipsum dolor. <span class="more">More...</span></p></article>

<div class="abs sect" style="left:37px;top:731px">Letest <em>News</em></div>
<div class="abs rule" style="left:37px;top:749px;width:646px"></div>
<div class="abs news-title" style="left:37px;top:766px">News Title Here</div>
<p class="abs news-text" style="left:37px;top:784px;width:646px">Lorem ipsum dolor sit ipusmLorem ipsum dolor sit ipusmLorem ipsum dolor sit ipusmLorem ipsum dolor sit ipusmLoremLorem ipsum dolor sit ipusmLorem <span class="more">More...</span></p>
<div class="abs rule" style="left:37px;top:831px;width:646px"></div>
<div class="abs news-title" style="left:38px;top:839px">News Title Here</div>
<div class="abs" role="img" aria-label="Illustration of a globe" style="left:35px;top:863px;width:83px;height:63px;border:1px solid #ddd;background:radial-gradient(circle,#5a6fc8 0,#3b4a9a 45%,#fff 70%)"></div>
<p class="abs news-text" style="left:127px;top:862px;width:556px">Lorem ipsum dolor sit ipusmLorem ipsum dolor sit ipusmLorem ipsum dolor sit ipusmLorem ipsum dolor sit ipusmLoremLorem ipsum dolor sit ipusmLorem Lorem ipsum dolor sit ipusmLorem ipsum dolor sit ipusmLorem ipsum dolor sit ipusmLorem ipsum dol or sit jdlkgjdlgjdlk ipusmLoremLorem ipsum dolor sit ipusmLorem <span class="more">More...</span></p>
<div class="abs rule" style="left:37px;top:941px;width:646px"></div>

<div class="abs sect" style="left:37px;top:951px">Letest <em>Photos</em></div>
<div class="gallery" style="left:35px;width:325px">
  <div class="shot" role="img" aria-label="Photo of a tropical beach, Pantai Biak" style="left:16px;width:142px"><span style="position:absolute;left:0;right:0;bottom:0;height:22px;background:rgba(255,255,255,.6);text-align:center;font-weight:700;font-size:12px;color:var(--navy);line-height:22px">Pantai Biak</span></div>
  <div class="shot" role="img" aria-label="Photo of sea and sky" style="left:174px;width:142px"></div>
</div>
<div class="arrow" style="left:23px;top:1020px"><svg width="20" height="20"><path d="M12 5l-6 5 6 5z" fill="#1a4f9c"/></svg></div>
<div class="arrow" style="left:346px;top:1020px"><svg width="20" height="20"><path d="M8 5l6 5-6 5z" fill="#d0103a"/></svg></div>

<div class="abs sect" style="left:379px;top:953px">Letest <em>videos</em></div>
<div class="gallery" style="left:379px;width:304px">
  <div class="shot" role="img" aria-label="Video still of sea and sky" style="left:7px;width:137px"><span class="play"></span></div>
  <div class="shot" role="img" aria-label="Video still of sea and sky" style="left:157px;width:137px"><span class="play"></span></div>
</div>

<aside class="box" style="top:727px;height:115px">
  <h4>Signup <em>Newsletter</em></h4>
  <div role="img" aria-label="Globe and newspaper illustration" style="position:absolute;left:3px;top:27px;width:62px;height:58px;border-radius:50%;background:radial-gradient(circle at 40% 40%,#9ed2f4,#1a73c0 60%,#fff 72%)"></div>
  <p style="position:absolute;left:84px;top:33px;width:116px;line-height:13px;text-align:justify;color:var(--muted)">ipusmLorem ipsum dolor sit ipusmLorem ipsum dolor sit</p>
  <div style="position:absolute;left:4px;top:88px;width:196px;height:23px;border:1px solid #ddd;display:flex">
    <span style="flex:1;padding-left:9px;line-height:21px;color:#ccc">Email here</span>
    <b style="background:var(--blue);color:#fff;font-size:11.5px;line-height:21px;padding:0 7px">SIGN UP</b>
  </div>
</aside>
<aside class="box" style="top:852px;height:245px">
  <h4>Meeting <em>Calendar</em></h4>
  <div class="event"><b>Date : 21-05-2012</b>Lorem ipsum dolor ispLorem ipsum dolor ispLorem ipsum dolor isp</div>
  <div class="event"><b>Date : 21-05-2012</b>Lorem ipsum dolor ispLorem ipsum dolor ispLorem ipsum dolor isp</div>
  <div class="event" style="border:0"><b>Date : 21-05-2012</b>Lorem ipsum dolor ispLorem ipsum dolor ispLorem ipsum dolor isp</div>
  <div style="position:absolute;right:12px;bottom:8px;color:var(--link);font-weight:700">More....</div>
</aside>

<footer class="abs footer">Copyright © 2012-2014 Harbourline Consulting Inc. TRELOS - Privacy policy<br>The information provided on this website is not official national government information and does not represent<br>the views or positions of the Global Agency for Vital Resource Aid or the national government.</footer>
<div class="abs footer-links">Home &nbsp;| &nbsp;About Us &nbsp;| &nbsp;Our Activities &nbsp;| &nbsp;Contact Us</div>
<div class="abs social" style="left:847px;background:#4fa8c8"></div>
<div class="abs social" style="left:874px;background:#3b5a9a"></div>
<div class="abs social" style="left:901px;background:#f08a1c"></div>
</body>
</html>
```